folding sales brochure

We need a brochure in the colors of orange, black and charcoal gray - our logo colors.
www.vennotraduxpartners

Strong, clean - and something eye catching.

We are looking for graphic images and photos that depict international business, written translation, live simultaneous interpretation for conferences & events with people communicating. We have some photos, but are open to others.

This brochure will generalize our companies services.
This brochure will be used for B2B as well as Trade Show booths.
Updates

Reason: Project has been extended to allow time for feedback and completion. Thank you all... some wonderful designs.

Thank you all for your designs - they were all creative in so many different ways, making the choice of just one very difficult.

regards,
Delia

Target Market(s)

Our target is large global corporate companies.

Industry/Entity Type

Events

Requirements
Must have
• company logo (will supply)
company website and address etc.

Our Type Font is: Helvetica Neue LT Std

All info needed can be found here: www.vennotraduxpartners
Should not have
• we feel globes and flags are overdone in the International marketplace - hopefully you can find something else to speak Global.

```html
<!DOCTYPE html>
<html lang="en">
<head>
<meta charset="utf-8">
<title>Vennotradux – Folding Sales Brochure</title>
<link href="https://fonts.googleapis.com/css2?family=Roboto:wght@300;400;500;700&family=Roboto+Condensed:wght@700&display=swap" rel="stylesheet">
<style>
  :root{
    --orange:#f39a1e;
    --orange-pale:#f7c37e;
    --charcoal:#333333;
    --ink:#111111;
    --grey-text:#6b6b6b;
    --ring:#b4b0ac;
    --paper:#ececec;
    --stage:#9a9a9a;
    --white:#ffffff;
  }
  *{margin:0;padding:0;box-sizing:border-box}
  html,body{width:1200px;height:1000px;overflow:hidden;background:var(--stage)}
  body{font-family:"Roboto",Arial,sans-serif;position:relative}
  .brochure{position:absolute;left:82px;top:80px;width:1043px;height:810px;overflow:hidden;
    background:linear-gradient(180deg,#f3f3f3 0%,var(--paper) 60%,#e2e2e2 100%)}
  .abs{position:absolute;z-index:3}
  .swoosh{position:absolute;left:0;top:0;z-index:0}
  .intro-panel{position:absolute;z-index:0;left:0;top:0;width:280px;height:325px;background:rgba(255,255,255,.45)}
  .section-title{font-size:20px;font-weight:700;color:var(--ink);letter-spacing:.2px}
  .section-title .hl{color:var(--orange)}
  .body-copy{font-size:10.4px;line-height:13.2px;color:var(--grey-text);font-weight:400;letter-spacing:-.1px}
  .body-copy p+p{margin-top:13px}
  .circle{position:absolute;border-radius:50%;z-index:1}
  .photo{position:absolute;border-radius:50%;z-index:2}
  .headline{font-family:"Roboto Condensed",Arial,sans-serif;font-weight:700;color:var(--white);font-size:46px;line-height:57px}
  .headline .hl{color:var(--orange)}
  .channels{font-size:17px;line-height:26px;color:#5b3b08;text-align:right;font-weight:400}
  .brace{font-family:"Roboto",Arial,sans-serif;font-weight:300;font-size:112px;line-height:1;color:var(--ink)}
  .motto{font-family:"Roboto Condensed",Arial,sans-serif;font-weight:700;color:var(--white)}
  .motto .small{font-family:"Roboto",Arial,sans-serif;font-weight:400;font-size:17px;color:var(--ink)}
  .url{font-size:14px;letter-spacing:4.2px;color:rgba(255,255,255,.85);font-weight:300}
  .solutions h3{font-size:13px;font-weight:700;color:var(--charcoal);margin-bottom:1px;letter-spacing:0}
  .tagline{font-size:17px;font-weight:700;color:var(--white);line-height:24px}
  .tagline .hl{color:var(--orange)}
  .brand{font-size:40px;font-weight:400;color:#707070;letter-spacing:-.5px}
  .contact{font-size:13px;font-weight:700;color:var(--ink);line-height:15px}
  .quote-box{left:558px;top:638px;width:460px;height:147px;background:var(--orange);box-shadow:3px 4px 6px rgba(0,0,0,.25)}
  .quote{font-size:10.6px;line-height:13.5px;color:var(--white);text-transform:uppercase;letter-spacing:.1px}
  .quote-source{font-size:10.6px;font-weight:700;color:var(--charcoal);margin-top:6px}
  .cta{font-size:15px;color:var(--ink);line-height:18px}
  .quote-photo{z-index:4}
</style>
</head>
<body>
<div class="brochure">

  <svg class="swoosh" width="1043" height="810" viewBox="0 0 1043 810" aria-hidden="true">
    <path d="M0 700 C 250 600, 560 640, 1043 560 L1043 810 L0 810Z" fill="#f7f7f7" opacity=".7"/>
    <path d="M0 745 C 300 640, 600 690, 1043 600" fill="none" stroke="#cfcfcf" stroke-width="2"/>
    <path d="M80 780 C 330 690, 640 730, 1043 650" fill="none" stroke="#ffffff" stroke-width="6"/>
    <path d="M200 810 C 420 740, 700 770, 1043 700" fill="none" stroke="#d8d8d8" stroke-width="3"/>
  </svg>

  <div class="intro-panel"></div>

  <!-- What we do -->
  <h2 class="abs section-title" style="left:40px;top:40px">WHAT <span class="hl">WE DO</span></h2>
  <div class="abs body-copy" style="left:40px;top:76px;width:230px">
    <p>"Language Solutions" are the services that allow communication to transcend language barriers. We begin with translators and interpreters and finish with the technology to bring it all together.</p>
    <p>Our solutions are just that: answers to problems. We meet your needs so you don't have to worry. Through Vennotradux, you communicate with your global audience with equal respect.</p>
    <p>We are a nationwide leader in live event language services, which includes simultaneous interpreters, interpreting equipment, and push-to-talk discussion systems. Our translation division has decades of experience and millions of words under its belt. Today, these services include a full range of studio services like voiceover and subtitles.</p>
  </div>

  <!-- Hero circle -->
  <div class="circle" style="left:282px;top:22px;width:290px;height:290px;background:var(--orange)"></div>
  <div class="photo" role="img" aria-label="Studio microphone with pop filter in a recording booth"
       style="left:282px;top:8px;width:280px;height:280px;background:radial-gradient(circle at 60% 40%,#8a8a8a 0%,#3a3a3a 45%,#151515 100%)"></div>
  <div class="abs headline" style="left:301px;top:65px">Helping<br>you<br><span class="hl">speak</span> to<br>the <span class="hl">world</span></div>

  <!-- Top right motto circle -->
  <div class="circle" style="left:688px;top:-108px;width:345px;height:345px;background:var(--ring)"></div>
  <div class="circle" style="left:706px;top:-68px;width:318px;height:318px;background:var(--orange)"></div>
  <div class="abs url" style="left:568px;top:15px">www.vennotraduxpartners.com</div>
  <div class="abs channels" style="left:700px;top:48px;width:126px">IN PERSON<br>ON PAPER<br>IN STUDIO<br>ON THE WEB</div>
  <div class="abs brace" style="left:830px;top:38px">}</div>
  <div class="abs motto" style="left:866px;top:28px">
    <div style="font-size:56px;line-height:58px">Let</div>
    <div style="font-size:32px;line-height:36px">everyone</div>
    <div style="font-size:32px;line-height:36px">speak, <span class="small">and</span></div>
    <div class="small" style="line-height:22px">be understood</div>
  </div>
  <div class="photo" role="img" aria-label="Antique world map in warm sepia tones"
       style="left:833px;top:196px;width:126px;height:126px;background:radial-gradient(circle at 40% 40%,#d9a45a 0%,#a2652a 60%,#5e3712 100%)"></div>

  <!-- More about our solutions -->
  <div class="circle" style="left:554px;top:188px;width:66px;height:66px;background:var(--orange-pale)"></div>
  <h2 class="abs section-title" style="left:554px;top:236px;line-height:26px">MORE<br>ABOUT OUR<br><span class="hl">SOLUTIONS...</span></h2>

  <div class="abs body-copy solutions" style="left:553px;top:320px;width:232px">
    <h3>Discussion systems</h3>
    Our Norvik Next Generation discussion systems offer the most secure, elegant and discrete solution on the market for roundtable and classroom-style discussions, push to talk, remote controlled and with optional automatic cameras.
  </div>
  <div class="abs body-copy solutions" style="left:553px;top:427px;width:232px">
    <h3>Conference interpreters</h3>
    We take special care to find the very best interpreters working today. These are interpreters who have extensive training and internationally recognized qualifications in the very specialized skill of simultaneous interpretation
  </div>
  <div class="abs body-copy solutions" style="left:553px;top:534px;width:232px">
    <h3>Rental &amp; sales</h3>
    If you need to supplement an existing system, we have a large inventory of systems, microphones, booths, transmitters and receivers – all ready to ship on a moment's notice.
  </div>
  <div class="abs body-copy solutions" style="left:802px;top:320px;width:215px">
    <h3>Streaming and fiber optic</h3>
    We offer recording and live internet streaming as well as remote interpretation streamed from our offices to your location.
  </div>
  <div class="abs body-copy solutions" style="left:802px;top:417px;width:205px">
    <h3>Fully-encapsulated booths</h3>
    We use industry standard, fully-encapsulated, soundproof interpreter booths that can accommodate up to three interpreters at once. We have one of the largest inventories of booths throughout the world.
  </div>
  <div class="abs body-copy solutions" style="left:801px;top:522px;width:228px">
    <h3>Across the map, around the globe</h3>
    Using our own transportation, we can deploy a system of any size to anywhere in the U.S. on short notice. In addition to serving the U.S., we also provide our services throughout the world.
  </div>

  <!-- Why choose us -->
  <div class="circle" style="left:-80px;top:325px;width:322px;height:322px;background:var(--ring)"></div>
  <div class="photo" role="img" aria-label="Conference stage with presenter and large projection screens"
       style="left:-56px;top:350px;width:275px;height:275px;background:radial-gradient(circle at 55% 60%,#5a6a80 0%,#2a2f3a 50%,#0d0f14 100%)"></div>
  <div class="abs tagline" style="left:24px;top:395px">More than <span class="hl">capable,</span><br>we make it <span class="hl">easy.</span></div>

  <div class="circle" style="left:183px;top:330px;width:80px;height:80px;background:var(--orange)"></div>
  <h2 class="abs section-title" style="left:211px;top:356px">WHY <span class="hl">CHOOSE US</span></h2>
  <div class="abs body-copy" style="left:261px;top:386px;width:232px">
    <p>Our approach is based on core principles of dedication, innovation and being prepared. Our clients' satisfaction matters the most, and we know that can only be guaranteed if we are prepared for any situation.</p>
    <p>Preparation begins with choosing the right people and adopting the best technologies. It continues through understanding our clients' needs and concerns, and having the foresight to anticipate surprises on the job.</p>
  </div>

  <div class="circle" style="left:240px;top:586px;width:118px;height:118px;background:#666"></div>
  <div class="photo" role="img" aria-label="Close-up of printed dictionary words in Spanish"
       style="left:248px;top:594px;width:102px;height:102px;background:radial-gradient(circle,#f4eee2 0%,#d8cdb8 100%)"></div>
  <div class="circle" style="left:360px;top:586px;width:118px;height:118px;background:var(--orange)"></div>
  <div class="photo" role="img" aria-label="Conference room with delegate microphones on tables"
       style="left:368px;top:594px;width:102px;height:102px;background:radial-gradient(circle,#b98a55 0%,#6d4a2a 100%)"></div>

  <!-- Brand and contact -->
  <div class="abs" style="left:30px;top:708px;display:flex;align-items:center;gap:10px">
    <div style="width:48px;height:48px;border-radius:50%;background:var(--orange)"></div>
    <div class="brand">vennotradux</div>
  </div>
  <div class="abs contact" style="left:94px;top:768px">Phone&nbsp;&nbsp;&nbsp;&nbsp;:+1 555 310 4821<br>Toll free :+1 888 555 0142</div>
  <div class="abs contact" style="left:280px;top:768px">Fax&nbsp;&nbsp;&nbsp;&nbsp;&nbsp;&nbsp;&nbsp;:+1 866 555 0187<br>Email&nbsp;&nbsp;&nbsp;:hello@venno.us</div>

  <!-- Testimonial -->
  <div class="abs quote-box">
    <div style="position:absolute;left:103px;top:12px;width:345px">
      <p class="quote">"I and everybody else who worked with me in the Bahamas was very happy and impressed with the great work you and your team provided in Nassau. I know that it often is quite challenging to work with us. "</p>
      <p class="quote-source">MAJOR INTERNATIONAL SPORTS ORGANIZATION</p>
    </div>
    <div class="cta" style="position:absolute;left:143px;top:90px">We want to give you the most<br>&nbsp;&nbsp;&nbsp;&nbsp;&nbsp;&nbsp;&nbsp;&nbsp;&nbsp;accurate quote that we can.</div>
    <div class="url" style="position:absolute;left:36px;top:123px;color:rgba(255,255,255,.7)">www.vennotraduxpartners.com</div>
  </div>
  <div class="photo quote-photo" role="img" aria-label="Interpreter console on a conference table"
       style="left:540px;top:612px;width:100px;height:100px;background:radial-gradient(circle,#8d7a63 0%,#4a3d30 100%)"></div>

</div>
</body>
</html>
```